Silverbrook Horizon Logo/Business Card

Project MUST include a logo with business card. See attached picture.

Logo is attached to brief but I'd like to add the tagline: "What you don't know that you don't know" Logo should also have an emblem that represents the Vortellan movie concept of red pill or blue pill (one in each hand). This emblem can be used with SilverBrook HoriZon or without.

Two sided card

Back can have the question mark logo that is attached

I'd like the background to be black.

On side have person's info:
Dorian Pelley
Trainer, Speaker, Author
p: 555-014-2297
e: d@silverbrookhorizon.example
www.silverbrookhorizon.example

Have find us on friendloop, quipstream (just logos)

Target Market(s)

People looking to know what they don't know, self development, personal growth

Industry/Entity Type

Movie

Requirements
Must have
• qr code
two sided

```html
<!DOCTYPE html>
<html lang="en">
<head>
<meta charset="utf-8">
<title>Silverbrook Horizon – Business Card</title>
<link rel="stylesheet" href="https://fonts.googleapis.com/css2?family=Oswald:wght@500&family=Source+Sans+3:wght@400;600;700&family=Cormorant+Garamond:wght@500&family=Gelasio&display=swap">
<style>
  :root {
    --stage: #ebe8e3;
    --card: #ffffff;
    --ink: #2f2f2f;
    --logo-grey: #555555;
    --orange: #e8681e;
    --silver-light: #f4f4f4;
    --silver-mid: #d2d2d2;
    --silver-dark: #a9a9a9;
    --chalk: #2c2d2f;
    --social: #2a7fc4;
    --label: #ffffff;
    --label-bg: #8a7a68;
  }
  * { box-sizing: border-box; margin: 0; padding: 0; }
  html, body {
    width: 1200px; height: 777px; overflow: hidden;
    background: var(--stage);
  }
  .stage { position: relative; width: 1200px; height: 777px; }

  .card {
    position: absolute;
    border-radius: 22px;
    background: var(--card);
    overflow: hidden;
    box-shadow: 0 4px 12px rgba(0,0,0,.18);
  }
  .card--front { left: 318px; top: 21px; width: 569px; height: 324px; }
  .card--back-orange { left: 11px; top: 375px; width: 572px; height: 324px; }
  .card--back-silver {
    left: 606px; top: 384px; width: 569px; height: 325px;
    background: linear-gradient(90deg, var(--silver-mid) 0%, var(--silver-light) 45%, #ffffff 60%, var(--silver-light) 80%, var(--silver-mid) 100%);
  }

  /* Front */
  .brand-name {
    position: absolute; left: 16px; top: 36px; width: 300px;
    font-family: "Oswald", sans-serif; font-weight: 500;
    color: var(--logo-grey);
    font-size: 50px; line-height: 70px; letter-spacing: 1px;
    text-transform: uppercase;
  }
  .tagline {
    position: absolute; left: 16px; top: 186px; width: 300px;
    font-family: "Gelasio", serif; font-size: 10.5px;
    color: var(--ink); text-align: center; letter-spacing: .2px;
    white-space: nowrap;
  }
  .contact {
    position: absolute; left: 338px; top: 116px;
    list-style: none;
    font-family: "Source Sans 3", sans-serif; font-size: 13.5px; color: var(--ink);
  }
  .contact li { display: flex; align-items: center; gap: 6px; height: 19px; white-space: nowrap; }
  .contact li.contact__web { font-weight: 700; }
  .contact svg { width: 12px; height: 12px; flex: none; }
  .person { position: absolute; left: 55px; top: 248px; text-align: center; width: 180px; font-family: "Source Sans 3", sans-serif; }
  .person__name { color: var(--orange); font-weight: 700; font-size: 20px; letter-spacing: .5px; text-transform: uppercase; line-height: 24px; }
  .person__role { color: var(--ink); font-size: 13px; }

  .wave { position: absolute; left: 0; bottom: 0; width: 100%; }

  /* Backs */
  .artwork {
    position: absolute;
    background: radial-gradient(circle at 50% 45%, #3a3b3e 0%, var(--chalk) 70%);
  }
  .card--back-orange .artwork { left: 47px; top: 59px; width: 150px; height: 168px; }
  .card--back-silver .artwork { left: 11px; top: 80px; width: 150px; height: 168px; }

  .find-us { position: absolute; font-family: "Cormorant Garamond", serif; font-weight: 500; color: var(--ink); font-size: 18px; }
  .card--back-orange .find-us { left: 446px; top: 108px; }
  .card--back-silver .find-us { left: 436px; top: 212px; }
  .find-us__title { display: block; margin-bottom: 8px; }
  .social { list-style: none; font-family: "Source Sans 3", sans-serif; font-size: 14px; font-weight: 600; color: var(--social); }
  .social li { display: flex; align-items: center; gap: 6px; height: 22px; }
  .social__dot { width: 14px; height: 14px; border-radius: 50%; background: var(--social); flex: none; }

  .rule { position: absolute; left: 0; top: 258px; width: 62%; height: 1px; background: linear-gradient(90deg, transparent, var(--silver-dark) 30%, var(--silver-dark) 65%, transparent); }

  .option-label {
    position: absolute; font-family: "Source Sans 3", sans-serif; font-size: 34px;
    color: var(--label); background: var(--label-bg);
    padding: 0 14px; border-radius: 6px; line-height: 46px;
  }
  .option-label--one { left: 184px; top: 720px; }
  .option-label--two { left: 806px; top: 716px; }
</style>
</head>
<body>
<main class="stage">

  <section class="card card--front" aria-label="Card front">
    <h1 class="brand-name">Silverbrook<br>Horizon</h1>
    <p class="tagline">"WHAT YOU DON'T KNOW THAT YOU DON'T KNOW"</p>
    <ul class="contact">
      <li>
        <svg viewBox="0 0 12 12" aria-hidden="true"><circle cx="6" cy="6" r="6" fill="var(--orange)"/><path d="M4 3l1.2 1.3-.6.8c.4.9 1 1.5 1.9 1.9l.8-.6L8.6 8 7.8 9C5.5 8.7 3.3 6.5 3 4.2z" fill="#fff"/></svg>
        555-014-2297
      </li>
      <li>
        <svg viewBox="0 0 12 12" aria-hidden="true"><circle cx="6" cy="6" r="6" fill="var(--orange)"/><circle cx="6" cy="6" r="2" fill="none" stroke="#fff" stroke-width="1.2"/></svg>
        d@silverbrookhorizon.example
      </li>
      <li class="contact__web">
        <svg viewBox="0 0 12 12" aria-hidden="true"><circle cx="6" cy="6" r="6" fill="var(--orange)"/><circle cx="6" cy="6" r="2.8" fill="none" stroke="#fff" stroke-width="1.2"/></svg>
        www.silverbrookhorizon.example
      </li>
    </ul>
    <div class="person">
      <p class="person__name">Dorian Pelley</p>
      <p class="person__role">Trainer, Speaker, Author</p>
    </div>
    <svg class="wave" viewBox="0 0 569 90" preserveAspectRatio="none" aria-hidden="true">
      <defs>
        <linearGradient id="frontWave" x1="0" x2="1">
          <stop offset="0" stop-color="#c9c9c9"/>
          <stop offset="1" stop-color="#a8a8a8"/>
        </linearGradient>
      </defs>
      <path d="M0 70 C140 80 260 60 380 30 C460 10 520 8 569 20 L569 90 L0 90 Z" fill="url(#frontWave)"/>
      <path d="M0 62 C150 72 270 50 390 22 C470 5 525 5 569 14 L569 22 C520 12 465 16 390 34 C270 62 150 80 0 72 Z" fill="#e4e4e4"/>
    </svg>
  </section>

  <section class="card card--back-orange" aria-label="Card back, option 1">
    <div class="artwork" role="img" aria-label="Question mark artwork with typographic lettering on a dark chalkboard"></div>
    <div class="find-us">
      <span class="find-us__title">Find us on</span>
      <ul class="social">
        <li><span class="social__dot"></span>friendloop</li>
        <li><span class="social__dot"></span>quipstream</li>
      </ul>
    </div>
    <svg class="wave" viewBox="0 0 572 90" preserveAspectRatio="none" aria-hidden="true">
      <path d="M0 66 C150 72 270 52 380 22 C460 2 520 0 572 10 L572 90 L0 90 Z" fill="#d9d9d9"/>
      <path d="M0 74 C150 80 280 60 390 34 C470 14 525 14 572 24 L572 90 L0 90 Z" fill="var(--orange)"/>
      <path d="M0 72 C150 78 275 56 388 30 C468 10 525 10 572 20 L572 24 C525 14 470 14 390 34 C280 60 150 80 0 76 Z" fill="#f2f2f2"/>
    </svg>
  </section>

  <section class="card card--back-silver" aria-label="Card back, option 2">
    <div class="rule" aria-hidden="true"></div>
    <div class="artwork" role="img" aria-label="Question mark artwork with typographic lettering on a dark chalkboard"></div>
    <div class="find-us">
      <span class="find-us__title">Find us on</span>
      <ul class="social">
        <li><span class="social__dot"></span>friendloop</li>
        <li><span class="social__dot"></span>quipstream</li>
      </ul>
    </div>
  </section>

  <p class="option-label option-label--one">Option 1</p>
  <p class="option-label option-label--two">Option 2</p>

</main>
</body>
</html>
```